Business Card Design Project

We are a construction company in Orange County, CA. We need a two sided business card. We would like the back to be our logo with web URL. Front should included Name, title, address, phone, fax and email address.

our address is
627 West Dorrance Blvd, Suite 308
Anaheim, CA 92718

Our logo files are attached.

Construction

```html
<!DOCTYPE html>
<html lang="en">
<head>
<meta charset="utf-8">
<title>Bramwell Business Card</title>
<link rel="stylesheet" href="https://fonts.googleapis.com/css2?family=Open+Sans:wght@400;700;800&display=swap">
<style>
  :root {
    --brand-blue: #1b4a7d;
    --accent-grey: #9a9a9a;
    --card-white: #ffffff;
    --ink: #333333;
    --backdrop: #ebe8e4;
  }
  * { box-sizing: border-box; margin: 0; padding: 0; }
  html, body { width: 1200px; height: 444px; overflow: hidden; }
  body {
    background: var(--backdrop);
    font-family: "Open Sans", Arial, sans-serif;
    color: var(--ink);
    position: relative;
  }
  .card {
    position: absolute;
    top: 75px;
    width: 515px;
    height: 295px;
    background: var(--card-white);
    box-shadow: 0 3px 8px rgba(0,0,0,0.25);
    overflow: hidden;
  }
  .card--front { left: 72px; }
  .card--back { left: 613px; }

  .wordmark {
    position: absolute;
    left: 0; right: 0;
    text-align: center;
    font-weight: 800;
    color: var(--brand-blue);
    font-size: 50px;
    letter-spacing: -0.5px;
    line-height: 1;
  }
  .card--front .wordmark { top: 72px; left: -10px; }
  .card--back .wordmark { top: 82px; }

  .band {
    position: absolute;
    top: 188px;
    left: 0;
    width: 494px;
    height: 25px;
    background: var(--brand-blue);
    color: var(--card-white);
    display: flex;
    align-items: center;
  }
  .band-tab {
    position: absolute;
    top: 188px;
    right: 0;
    width: 25px;
    height: 25px;
    background: var(--accent-grey);
  }
  .band--name { justify-content: center; padding-left: 90px; }
  .holder-name { font-weight: 700; font-size: 16px; letter-spacing: 0.2px; }
  .holder-title {
    font-size: 14px;
    margin-left: 6px;
    padding-left: 6px;
    border-left: 1px solid rgba(255,255,255,0.7);
    line-height: 21px;
  }
  .band--web { justify-content: center; font-size: 13px; letter-spacing: 2px; }

  .contact-row {
    position: absolute;
    top: 231px;
    left: 10px; right: 10px;
    display: flex;
    justify-content: center;
    gap: 11px;
    font-size: 13px;
    white-space: nowrap;
  }
  .contact-item { display: flex; align-items: center; gap: 3px; }
  .contact-item svg { width: 10px; height: 10px; fill: var(--ink); flex: none; }
  .address {
    position: absolute;
    top: 259px;
    left: 0; right: 0;
    text-align: center;
    font-size: 13px;
    white-space: nowrap;
  }
</style>
</head>
<body>
  <section class="card card--front" aria-label="Card front">
    <div class="wordmark">BRAMWELL</div>
    <div class="band band--name">
      <span class="holder-name">YOUR NAME</span>
      <span class="holder-title">Title</span>
    </div>
    <div class="band-tab"></div>
    <div class="contact-row">
      <span class="contact-item">
        <svg viewBox="0 0 12 12" aria-hidden="true"><circle cx="6" cy="6" r="6"/><path d="M4 3.2l1 1.6-.6.6c.4.9 1.1 1.6 2 2l.6-.6 1.6 1-.6 1.2C5.5 9 3 6.5 2.9 3.8z" fill="#fff"/></svg>0912345678
      </span>
      <span class="contact-item">
        <svg viewBox="0 0 12 12" aria-hidden="true"><path d="M1 5c0-2 2.5-3 5-3s5 1 5 3l-2 .6-.5-1.4H3.5L3 5.6z"/><rect x="2.5" y="6" width="7" height="4.5" rx="1"/></svg>0912345678
      </span>
      <span class="contact-item">
        <svg viewBox="0 0 12 12" aria-hidden="true"><rect x="1" y="3" width="10" height="6.5"/><path d="M1 3l5 3.5L11 3" stroke="#fff" stroke-width="1" fill="none"/></svg>info@bramwell.com
      </span>
      <span class="contact-item">
        <svg viewBox="0 0 12 12" aria-hidden="true"><circle cx="6" cy="6" r="5.5"/><path d="M.5 6h11M6 .5v11M6 .5c-2.5 3-2.5 8 0 11M6 .5c2.5 3 2.5 8 0 11" stroke="#fff" stroke-width=".8" fill="none"/></svg>www.bramwell.com
      </span>
    </div>
    <p class="address">627 West Dorrance Blvd, Suite 308 Anaheim, CA 92718</p>
  </section>

  <section class="card card--back" aria-label="Card back">
    <div class="wordmark">BRAMWELL</div>
    <div class="band band--web">www.bramwell.com</div>
    <div class="band-tab"></div>
  </section>
</body>
</html>
```